Social Media Graphics - Oakline Push REVISED

Create 6-7 individual social media graphics (square size) to encourage folks to join our online course called:

The Harvest Ledger Circle
How to Launch a Multi-Million Business From Scratch
Sign Up Today!

IMPORTANT: Make the largest and most prominent text on the graphic be: How to Launch a Multi-Million Business From Scratch

For the color scheme of the graphics, let's try a blue color palette; make sure the graphics appeal to both men and women

Make sure each graphic contains 1 of the 3 pics attached (crop pic as needed); and make sure one of the graphics is all TEXT only.

Target Market(s)

men and women looking to start a business

Industry/Entity Type

Entrepreneurship

Colors
0054AA
0677BA
7BADD7
CADEEF
E8F1F8

Requirements
Must have
• All the text and use the 3 pics provided; one graphic can be all text; Simple, modern design that's easy to read

```html
<!DOCTYPE html>
<html lang="en">
<head>
<meta charset="UTF-8">
<title>The Harvest Ledger Circle – Sign Up</title>
<link rel="stylesheet" href="https://fonts.googleapis.com/css2?family=Archivo:ital,wght@1,900&family=Montserrat:wght@600;700&display=swap">
<style>
  :root {
    --navy-deep: #050a5c;
    --navy: #0b1a8f;
    --royal: #1f3fb0;
    --sky: #4f7fd6;
    --button-blue: #2666ad;
    --button-blue-light: #3a82c6;
    --gold-light: #ffe08a;
    --gold: #e6b443;
    --gold-dark: #b97d1c;
    --white: #ffffff;
  }
  html, body {
    margin: 0;
    padding: 0;
    width: 1200px;
    height: 1200px;
    overflow: hidden;
    background: var(--white);
  }
  .graphic {
    position: relative;
    width: 1200px;
    height: 1200px;
    overflow: hidden;
  }
  .silk-backdrop {
    position: absolute;
    inset: 0;
    background:
      linear-gradient(125deg,
        var(--navy) 0%,
        var(--royal) 18%,
        var(--navy) 30%,
        var(--sky) 45%,
        var(--royal) 55%,
        var(--sky) 68%,
        var(--navy) 80%,
        var(--navy-deep) 100%);
  }
  .eyebrow {
    position: absolute;
    top: 118px;
    left: 0;
    width: 100%;
    margin: 0;
    text-align: center;
    font-family: "Montserrat", sans-serif;
    font-weight: 700;
    font-size: 40px;
    letter-spacing: 1px;
    color: var(--white);
    text-transform: uppercase;
  }
  .headline {
    position: absolute;
    top: 270px;
    left: 0;
    width: 100%;
    margin: 0;
    text-align: center;
    font-family: "Archivo", sans-serif;
    font-style: italic;
    font-weight: 900;
    color: var(--white);
    letter-spacing: -2px;
  }
  .headline span { display: block; }
  .headline .line-small { font-size: 92px; line-height: 118px; }
  .headline .line-large { font-size: 128px; line-height: 140px; }
  .headline .line-first { line-height: 110px; }
  .cta {
    position: absolute;
    left: 234px;
    top: 872px;
    width: 694px;
    height: 212px;
  }
  .cta svg { position: absolute; inset: 0; }
  .cta-label {
    position: absolute;
    inset: 0;
    display: flex;
    flex-direction: column;
    align-items: center;
    justify-content: center;
    font-family: "Montserrat", sans-serif;
    color: var(--white);
    text-transform: uppercase;
  }
  .cta-main { font-weight: 600; font-size: 88px; line-height: 82px; letter-spacing: 1px; }
  .cta-sub { font-weight: 700; font-size: 48px; line-height: 52px; }
</style>
</head>
<body>
  <div class="graphic">
    <div class="silk-backdrop" role="img" aria-label="Flowing royal blue satin fabric background"></div>

    <p class="eyebrow">The Harvest Ledger Circle</p>

    <h1 class="headline">
      <span class="line-small line-first">How to Launch</span>
      <span class="line-large">a Multi-Million</span>
      <span class="line-large">Business</span>
      <span class="line-small">From Scratch</span>
    </h1>

    <div class="cta">
      <svg viewBox="0 0 694 212" width="694" height="212" aria-hidden="true">
        <defs>
          <linearGradient id="gold-frame" x1="0" y1="0" x2="1" y2="1">
            <stop offset="0" stop-color="var(--gold-light)"/>
            <stop offset="0.35" stop-color="var(--gold)"/>
            <stop offset="0.55" stop-color="var(--gold-dark)"/>
            <stop offset="0.8" stop-color="var(--gold-light)"/>
            <stop offset="1" stop-color="var(--gold)"/>
          </linearGradient>
          <linearGradient id="button-fill" x1="0" y1="0" x2="1" y2="0">
            <stop offset="0" stop-color="var(--button-blue)"/>
            <stop offset="0.5" stop-color="var(--button-blue-light)"/>
            <stop offset="1" stop-color="var(--button-blue)"/>
          </linearGradient>
        </defs>
        <polygon points="28,0 666,0 694,28 694,184 666,212 28,212 0,184 0,28" fill="url(#gold-frame)"/>
        <polygon points="34,18 660,18 676,34 676,178 660,194 34,194 18,178 18,34" fill="url(#button-fill)"/>
        <polygon points="40,27 654,27 667,40 667,172 654,185 40,185 27,172 27,40" fill="none" stroke="url(#gold-frame)" stroke-width="2"/>
      </svg>
      <div class="cta-label">
        <span class="cta-main">Sign Up</span>
        <span class="cta-sub">Today</span>
      </div>
    </div>
  </div>
</body>
</html>
```